Suds Haven Laundromat Wordpress Design

We need a Wordpress website design for our laundromat, Suds Haven Atlanta, at www.sudshavenatlanta-example.com. We would like to have 6 pages: Home, About Us, Services, Locations, Reviews and Contact us. We will provide content for the text on each page. What we do: We are a full service laundromat that provides dry cleaning drop off, professional laundry services, wash dry fold and self service laundry to the local community. We would like to use the color scheme from our logo to convey a warm, safe, and bright business that caters to its diverse community.
Updates

I like the structure of this laundromat website: http://www.washtroveusa-example.com/ Using my logo and color scheme in the above referenced website is what. Am looking for. The photos attached to the project with the female model should be used as a primary focus and supplemented by actual photos of the equipment.

Target Market(s)

Our target market is a diverse group of people from Midtown Atlanta - LGBTQ community /Locals/Regulars that have been coming to laundromat for 30 years.

Industry/Entity Type

Laundromat

Coding

Coded - Design and coding required

Number of Pages Required

5+ page

Font styles to use
Sans Serif

Colors
0054AA
0677BA
7BADD7
CADEEF
E8F1F8

Requirements
Must have
• Feature this video on the main page: https://videohost-example.com/xq7Rm2bPz4k

```html
<!DOCTYPE html>
<html lang="en">
<head>
<meta charset="utf-8">
<title>Suds Haven – About Us</title>
<link rel="stylesheet" href="https://fonts.googleapis.com/css2?family=Bebas+Neue&family=Montserrat:wght@400;500;600&display=swap">
<style>
:root{
  --blue-deep:#0054AA;
  --blue-mid:#0677BA;
  --blue-bright:#0aace4;
  --blue-soft:#7BADD7;
  --blue-pale:#CADEEF;
  --ink:#222;
  --text:#333;
  --band:#f1f5f8;
  --card:#e2e9ed;
  --footer:#2f4664;
  --footer-line:#4a5f7c;
  --white:#fff;
}
*{box-sizing:border-box;margin:0;padding:0}
html,body{width:700px;height:1200px;overflow:hidden;background:var(--white)}
body{position:relative;font-family:"Montserrat",sans-serif;color:var(--text)}

/* header */
.site-header{position:absolute;left:0;top:0;width:700px;height:44px;background:var(--white);z-index:2}
.brand{position:absolute;left:60px;top:12px;display:flex;align-items:center;gap:5px;font-weight:600;font-size:15px;color:var(--blue-deep);white-space:nowrap}
.brand-dot{width:10px;height:10px;border-radius:50%;background:var(--blue-bright)}
.main-nav{position:absolute;top:20px;left:0;font-size:7.4px;font-weight:500;color:var(--ink);letter-spacing:.2px}
.main-nav span{position:absolute;white-space:nowrap}
.main-nav .current{font-weight:600}
.nav-marker{position:absolute;left:290px;top:42px;width:39px;height:2px;background:var(--blue-deep)}
.nav-divider{position:absolute;left:600px;top:11px;width:1px;height:22px;background:var(--blue-deep)}
.social-dot{position:absolute;top:19px;width:7px;height:7px;border-radius:50%;background:var(--ink)}

/* hero */
.hero{position:absolute;left:0;top:44px}

.breadcrumb{position:absolute;left:95px;top:294px;font-size:7.4px;font-weight:500;color:var(--ink)}
.breadcrumb b{color:var(--blue-deep);font-weight:600}

/* about */
.about-photo{position:absolute;left:104px;top:396px;width:180px;height:180px;border-radius:50%;
  background:linear-gradient(180deg,#cfe6ea 0%,#d9d5c6 35%,#5a8fc4 70%,#d8d4c8 100%)}
.section-title{font-family:"Bebas Neue",sans-serif;color:var(--ink);letter-spacing:.2px;line-height:1}
.section-title em{font-style:normal;color:var(--blue-deep)}
.about-title{position:absolute;left:334px;top:372px;font-size:21px}
.title-rule{position:absolute;height:2px;width:26px;background:var(--blue-bright)}
.about-copy{position:absolute;left:334px;top:407px;width:276px;font-size:7.7px;line-height:15.8px;color:var(--ink)}
.about-copy p+p{margin-top:2.5px}
.cta{position:absolute;left:334px;top:541px;width:87px;height:25px;background:var(--blue-bright);color:var(--white);font-size:7.4px;font-weight:600;display:flex;align-items:center;justify-content:center}

/* why */
.why{position:absolute;left:0;top:632px;width:700px;height:261px;background:var(--band)}
.why-title{position:absolute;left:0;width:700px;text-align:center;top:46px;font-size:21px}
.feature{position:absolute;width:164px;height:61px;background:var(--card);border-radius:3px;padding:13px 8px 0 24px;font-size:9px;line-height:15px;color:var(--ink)}
.feature svg{position:absolute;left:7px;top:14px}

/* footer */
.site-footer{position:absolute;left:0;top:893px;width:700px;height:307px;background:var(--footer);color:var(--white)}
.footer-brand{position:absolute;left:0;width:700px;top:58px;display:flex;justify-content:center;align-items:center;gap:8px;font-weight:600;font-size:22px}
.footer-brand i{width:14px;height:14px;border-radius:50%;border:2px solid var(--white);display:block}
.footer-rule{position:absolute;height:1px;background:var(--footer-line)}
.footer-nav{position:absolute;top:134px;left:0;font-size:9px}
.footer-nav span{position:absolute;white-space:nowrap}
.footer-social{position:absolute;top:131px;width:18px;height:18px;border-radius:50%;background:var(--white)}
.contact{position:absolute;font-size:8px;line-height:14px}
.contact svg{position:absolute;left:-18px;top:1px}
.hours{position:absolute;left:357px;top:180px;font-size:8px;line-height:14px}
.hours .note{color:var(--blue-bright);font-weight:500;margin-bottom:5px}
.copyright{position:absolute;left:0;width:700px;top:270px;text-align:center;font-size:7.2px}
.copyright b{font-weight:600}
</style>
</head>
<body>

<header class="site-header">
  <div class="brand"><span class="brand-dot"></span>Suds Haven</div>
  <nav class="main-nav">
    <span style="left:243px">HOME</span>
    <span class="current" style="left:290px">ABOUT US</span>
    <span style="left:353px">SERVICES</span>
    <span style="left:413px">LOCATION</span>
    <span style="left:482px">REVIEWS</span>
    <span style="left:540px">CONTACT US</span>
  </nav>
  <div class="nav-marker"></div>
  <div class="nav-divider"></div>
  <div class="social-dot" style="left:612px"></div>
  <div class="social-dot" style="left:627px"></div>
</header>

<svg class="hero" width="700" height="245" viewBox="0 44 700 245">
  <defs>
    <linearGradient id="heroFill" x1="0" y1="0" x2="1" y2="1">
      <stop offset="0" stop-color="#8a9a6a"/>
      <stop offset=".35" stop-color="#d8d6c8"/>
      <stop offset=".7" stop-color="#cfcab8"/>
      <stop offset="1" stop-color="#a89f86"/>
    </linearGradient>
  </defs>
  <path role="img" aria-label="Photo of the laundromat interior with rows of washers and dryers" d="M0 44H700V234Q360 292 0 236Z" fill="url(#heroFill)"/>
  <path d="M0 244Q330 304 670 247Q330 292 0 240Z" fill="var(--blue-deep)"/>
</svg>

<div class="breadcrumb">HOME / <b>ABOUT US</b></div>

<div class="about-photo" role="img" aria-label="Photo of a model in a blue dress seated in front of the washers"></div>

<h2 class="section-title about-title">About <em>Us</em></h2>
<div class="title-rule" style="left:334px;top:396px"></div>
<div class="about-copy">
  <p>Suds Haven is family-owned laundromat that has been serving Midtown, GA for over 45 years. We are proud to offer high quality and convenient services to the area residents and business owners and strive to keep our customers clothing in tip top shape.</p>
  <p>Whether you have commercial laundry needs, are washing clothes for your family, or want to relax that weekend and have us pick up and wash/dry/fold for you, the professionals at Suds Haven are ready to meet your goals.</p>
</div>
<div class="cta">Contact Us Today</div>

<section class="why">
  <h2 class="section-title why-title">Why <em>Choose Us</em></h2>
  <div class="title-rule" style="left:337px;top:70px"></div>

  <div class="feature" style="left:94px;top:85px"><svg width="11" height="11" viewBox="0 0 11 11"><circle cx="5.5" cy="5.5" r="4.5" fill="none" stroke="var(--blue-mid)"/><path d="M3 5.5l2 2 5-6" fill="none" stroke="var(--blue-mid)" stroke-width="1.2"/></svg>In Business over 45 years</div>
  <div class="feature" style="left:268px;top:85px"><svg width="11" height="11" viewBox="0 0 11 11"><circle cx="5.5" cy="5.5" r="4.5" fill="none" stroke="var(--blue-mid)"/><path d="M3 5.5l2 2 5-6" fill="none" stroke="var(--blue-mid)" stroke-width="1.2"/></svg>Voted "BEST COIN LAUNDRY" - Multiple years</div>
  <div class="feature" style="left:441px;top:85px"><svg width="11" height="11" viewBox="0 0 11 11"><circle cx="5.5" cy="5.5" r="4.5" fill="none" stroke="var(--blue-mid)"/><path d="M3 5.5l2 2 5-6" fill="none" stroke="var(--blue-mid)" stroke-width="1.2"/></svg>One of Atlanta's First, Finest, &amp; Friendliest Coin Laundries</div>
  <div class="feature" style="left:94px;top:155px"><svg width="11" height="11" viewBox="0 0 11 11"><circle cx="5.5" cy="5.5" r="4.5" fill="none" stroke="var(--blue-mid)"/><path d="M3 5.5l2 2 5-6" fill="none" stroke="var(--blue-mid)" stroke-width="1.2"/></svg>The best Wash-Dry-Fold in Town</div>
  <div class="feature" style="left:268px;top:155px"><svg width="11" height="11" viewBox="0 0 11 11"><circle cx="5.5" cy="5.5" r="4.5" fill="none" stroke="var(--blue-mid)"/><path d="M3 5.5l2 2 5-6" fill="none" stroke="var(--blue-mid)" stroke-width="1.2"/></svg>Cool - Comfortable - Clean</div>
  <div class="feature" style="left:441px;top:155px"><svg width="11" height="11" viewBox="0 0 11 11"><circle cx="5.5" cy="5.5" r="4.5" fill="none" stroke="var(--blue-mid)"/><path d="M3 5.5l2 2 5-6" fill="none" stroke="var(--blue-mid)" stroke-width="1.2"/></svg>Over 50 Well Maintained Machines</div>
</section>

<footer class="site-footer">
  <div class="footer-brand"><i></i>SUDS HAVEN</div>
  <div class="footer-rule" style="left:180px;top:116px;width:340px"></div>
  <nav class="footer-nav">
    <span style="left:148px">Home</span>
    <span style="left:197px">About Us</span>
    <span style="left:260px">Services</span>
    <span style="left:320px">Location</span>
    <span style="left:384px">Reviews</span>
    <span style="left:444px">Contact Us</span>
  </nav>
  <div class="footer-social" style="left:512px"></div>
  <div class="footer-social" style="left:538px"></div>
  <div class="footer-rule" style="left:180px;top:163px;width:340px"></div>

  <div class="contact" style="left:161px;top:180px;width:190px">
    <svg width="11" height="12" viewBox="0 0 11 12"><path d="M5.5 11S1.5 7 1.5 4.5a4 4 0 0 1 8 0C9.5 7 5.5 11 5.5 11z" fill="none" stroke="var(--white)" stroke-width=".9"/><circle cx="5.5" cy="4.5" r="1.4" fill="none" stroke="var(--white)" stroke-width=".9"/></svg>
    Brookfield Commons Shopping Center, 1820 Maple Row Ave NE., # 406, Atlanta, GA 30399
  </div>
  <div class="contact" style="left:161px;top:216px">
    <svg width="11" height="11" viewBox="0 0 11 11"><path d="M2 1l2 .5.6 2.3-1.2 1a6 6 0 0 0 2.8 2.8l1-1.2 2.3.6.5 2c-4 1-9-4-8-8z" fill="none" stroke="var(--white)" stroke-width=".9"/></svg>
    (555) 014-3517
  </div>
  <div class="hours">
    <p class="note">Delivery Available* please contact us for details</p>
    <p>Covid 19 hours - open 7 days a week 8 am to 8 pm</p>
    <p>Last wash begins 6:30 pm</p>
  </div>
  <div class="footer-rule" style="left:94px;top:244px;width:512px"></div>
  <p class="copyright">Copyright © 2021 <b>Suds Haven Atlanta</b>. All Rights Reserved.</p>
</footer>

</body>
</html>
```